Letterhead for Conveyancing Company

Use existing logo to create a letterhead for a conveyancing company. Must be able to be used in Microsoft Word. Easy to read and professional.
Contact information to be at the bottom.
Bright Oak Conveyancing Pty Ltd
ACN 621 984 736PO Box 535 Campbelltown SA 5074
Mobile - 0461739286
Web address - www.brightoakconveyancing.com.au

Requirements
Must have
• Logo and contact details.
• Simple and professional.

```html
<!DOCTYPE html>
<html lang="en">
<head>
<meta charset="utf-8">
<title>Bright Oak Conveyancing – Letterhead</title>
<link href="https://fonts.googleapis.com/css2?family=Roboto:wght@400;500;700&display=swap" rel="stylesheet">
<style>
  :root {
    --backdrop: #4e4b4a;
    --paper: #fafafa;
    --brand: #e0409b;
    --ink: #6b6b6b;
    --ink-strong: #555555;
    --watermark: #f0f0f0;
  }
  * { margin: 0; padding: 0; box-sizing: border-box; }
  html, body { width: 1062px; height: 1200px; overflow: hidden; }
  body { background: var(--backdrop); font-family: 'Roboto', Arial, sans-serif; color: var(--ink); }
  .letterhead {
    position: absolute; left: 106px; top: 0;
    width: 849px; height: 1200px;
    background: var(--paper);
  }
  .company-name {
    position: absolute; left: 53px; top: 77px;
    font-size: 17.5px; font-weight: 700; color: var(--brand); letter-spacing: 0.1px;
  }
  .contact { position: absolute; left: 53px; top: 119px; list-style: none; font-size: 13px; letter-spacing: 0.3px; }
  .contact li { display: flex; align-items: center; height: 21px; }
  .contact svg { width: 11px; height: 11px; margin-right: 11px; fill: var(--brand); flex: none; }
  .contact .acn { margin-left: 14px; display: inline-flex; align-items: center; }
  .contact .acn svg { margin-right: 8px; }
  .contact .label { color: var(--brand); margin-right: 4px; }
  .header-rule { position: absolute; left: 0; top: 0; }
  .brand-mark {
    position: absolute; right: 64px; top: 76px;
    text-align: right; color: var(--brand); font-weight: 700;
    font-size: 34px; line-height: 1.05; letter-spacing: 0.5px;
  }
  .brand-watermark {
    position: absolute; left: 140px; top: 400px;
    color: var(--watermark); font-weight: 700; font-size: 150px; line-height: 0.95;
  }
  .letter-body { position: absolute; left: 53px; top: 310px; width: 743px; font-size: 13.5px; line-height: 19.3px; }
  .date { margin-bottom: 37px; }
  .recipient { margin-bottom: 37px; }
  .recipient strong { font-weight: 500; color: var(--ink-strong); }
  .salutation { margin-bottom: 19px; }
  .letter-body p.copy { text-align: justify; margin-bottom: 19px; letter-spacing: -0.3px; }
  .sign-off { position: absolute; left: 53px; top: 968px; font-size: 13.5px; }
  .sign-off .name { font-weight: 500; color: var(--ink-strong); }
  .signature {
    width: 190px; height: 40px; margin: 8px 0 8px -18px;
    background: linear-gradient(90deg, rgba(44,74,130,0.15), rgba(44,74,130,0.05));
    border-radius: 4px;
  }
</style>
</head>
<body>
<main class="letterhead">
  <svg class="header-rule" width="849" height="260" aria-hidden="true">
    <path d="M53 109 H403 Q416 109 428 118 L548 221 Q557 229 570 229 H789" fill="none" stroke="var(--brand)" stroke-width="1.6"/>
  </svg>

  <h1 class="company-name">Bright Oak Conveyancing Pty Ltd</h1>
  <ul class="contact">
    <li>
      <svg viewBox="0 0 12 12"><path d="M1 4.5 Q6 1 11 4.5 L10 6 L8 5 V4 Q6 3.2 4 4 V5 L2 6 Z M3 6.5 H9 L10 10.5 H2 Z"/></svg>
      046 173 9286
      <span class="acn">
        <svg viewBox="0 0 12 12"><path d="M3 1h1.5l-.4 2.5h2.8L7.3 1h1.5l-.4 2.5H11V5H8.2l-.3 2H11v1.5H7.7L7.3 11H5.8l.4-2.5H3.4L3 11H1.5l.4-2.5H1V7h1.1l.3-2H1V3.5h1.6zM3.9 5l-.3 2h2.8l.3-2z"/></svg>
        <span class="label">ACN</span>583 217 469
      </span>
    </li>
    <li>
      <svg viewBox="0 0 12 12"><path d="M6 .5a5.5 5.5 0 1 0 0 11 5.5 5.5 0 0 0 0-11zm0 1.3c.6.6 1.1 1.6 1.3 3.4H4.7C4.9 3.4 5.4 2.4 6 1.8zM1.9 6.6h1.6c.1 1.3.4 2.4.8 3.2A4.2 4.2 0 0 1 1.9 6.6zm0-1.4a4.2 4.2 0 0 1 2.4-3.2c-.4.8-.7 1.9-.8 3.2zm4.1 5c-.6-.6-1.1-1.6-1.3-3.6h2.6c-.2 2-.7 3-1.3 3.6zm1.7-.4c.4-.8.7-1.9.8-3.2h1.6a4.2 4.2 0 0 1-2.4 3.2zm.8-4.6c-.1-1.3-.4-2.4-.8-3.2a4.2 4.2 0 0 1 2.4 3.2z"/></svg>
      www.brightoakconveyancing.com.au
    </li>
    <li>
      <svg viewBox="0 0 12 12"><path d="M6 .5A4 4 0 0 0 2 4.5C2 7.5 6 11.5 6 11.5s4-4 4-7A4 4 0 0 0 6 .5zm0 5.6a1.6 1.6 0 1 1 0-3.2 1.6 1.6 0 0 1 0 3.2z"/></svg>
      PO Box 871 Marlowdale SA 5096
    </li>
  </ul>

  <div class="brand-mark">Bright Oak<br>Conveyancing</div>
  <div class="brand-watermark" aria-hidden="true">Bright<br>Oak</div>

  <section class="letter-body">
    <p class="date">30/20/2016</p>
    <p class="recipient"><strong>Mr. XYZ Smith</strong><br>123, Street No. 123,<br>City Name<br>Pincode-123456</p>
    <p class="salutation">Dear Sir,</p>
    <p class="copy">Lorem Ipsum is simply dummy text of the printing and typesetting industry. Lorem Ipsum has been the industry's standard dummy text ever since the 1500s, when an unknown printer took a galley of type and scrambled it to make a type specimen book. It has survived not only five centuries, but also the leap into electronic typesetting, remaining essentially unchanged. It was popularised in the 1960s with the release of Lettrane sheets containing Lorem Ipsum passages, and more recently with desktop publishing software like Folio Layout including versions of Lorem Ipsum.</p>
    <p class="copy">Lorem Ipsum is simply dummy text of the printing and typesetting industry. Lorem Ipsum has been the industry's standard dummy text ever since the 1500s, when an unknown printer took a galley of type and scrambled it to make a type specimen book. It has survived not only five centuries, but also the leap into electronic typesetting, remaining essentially unchanged. It was popularised in the 1960s with the release of Lettrane sheets containing Lorem Ipsum passages, and more recently with desktop publishing software like Folio Layout including versions of Lorem Ipsum.</p>
    <p class="copy">Lorem Ipsum is simply dummy text of the printing and typesetting industry. Lorem Ipsum has been the industry's standard dummy text ever since the 1500s, when an unknown printer took a galley of type and scrambled it to make a type specimen book.</p>
    <p class="copy">Lorem Ipsum is simply dummy text of the printing and typesetting industry. Lorem Ipsum has been the industry's standard dummy text ever since the 1500s, when an unknown printer took a galley of type and scrambled it to make a type specimen book.</p>
  </section>

  <footer class="sign-off">
    <p class="name">Your Name</p>
    <div class="signature" role="img" aria-label="Handwritten signature"></div>
    <p class="role">CEO &nbsp;|&nbsp; Owner</p>
  </footer>
</main>
</body>
</html>
```